Agriculture farming Hemp and CBD

The logo is in works with your company now, should be ready in a few days. We have our Domain (kestrelbrookhollow.com) We would like to see incorporated seed to growth, but not necessary. we would like to nature colors and some black and green. we have our farm and will be growing and selling HEMP and CBD we are based in the state of Virginia. Would like to incorporate the words pause, play, rewind if possible but not necessary.

Target Market(s)

20 years old to elderly

Coding

Coded - Design and coding required

Number of Pages Required

3 page

Font styles to use
Serif

Requirements
Must have
• I'm not sure on the must haves, we are open to any ideas, we would definitely like to see Hemp and CBD included, may the life cycle of seed to plant. We must have a pop up asking if you are 20 years old before they can enter our site and to view or purchase our product. I want the design to be totally different than what i uploaded.
Nice to have
• Would like to see natural colors as well as black and green
Should not have
• I want

```html
<!DOCTYPE html>
<html lang="en">
<head>
<meta charset="utf-8">
<title>Kestrel Brook Hollow — Hemp and CBD</title>
<link rel="stylesheet" href="https://fonts.googleapis.com/css2?family=Oswald:wght@500;600&family=Tinos:wght@400;700&family=Montserrat:wght@400;600;700&display=swap">
<style>
:root{
  --stage:#cfcfcf;
  --bar:#141414;
  --nav:#0d3a10;
  --green:#0b3f0e;
  --green-2:#0e4812;
  --accent:#f2df36;
  --line:#4b9a34;
  --white:#ffffff;
  --soft:#d8e8d0;
  --cta:#1fa52c;
  --red:#e3232b;
  --badge:#0a340c;
  --badge-ring:#e4efe0;
}
*{box-sizing:border-box;margin:0;padding:0}
html,body{width:1200px;height:2708px;overflow:hidden;background:var(--stage)}
body{position:relative;font-family:'Montserrat',sans-serif;color:var(--white)}
.page{position:absolute;top:28px;width:540px;height:2650px;background:var(--green);overflow:hidden}
.page--gated{left:42px}
.page--open{left:619px}

.topbar{height:26px;background:var(--bar);display:flex;align-items:center;justify-content:space-between;padding:0 50px}
.social{display:flex;gap:4px}
.social span{width:14px;height:14px;border:1px solid #bbb;border-radius:50%}
.brand{font-weight:700;font-size:12px;color:var(--white);letter-spacing:-.2px}
.tools{display:flex;gap:7px;align-items:center}
.mainnav{height:25px;background:var(--nav);display:flex;justify-content:center;align-items:center;gap:19px;font-size:6.5px;font-weight:700;text-transform:uppercase}
.mainnav .on{text-decoration:underline}

.hero{position:relative;height:272px;text-align:center;
  background:radial-gradient(circle at 28% 22%,#6fa84a 0,transparent 28%),radial-gradient(circle at 70% 55%,#5c9a3a 0,transparent 32%),radial-gradient(circle at 45% 80%,#3f7a2a 0,transparent 30%),linear-gradient(160deg,#2b6020 0%,#183f14 55%,#0c260b 100%)}
.hero h1{position:absolute;top:100px;left:0;right:0;font-family:'Oswald',sans-serif;font-weight:600;font-size:24px;letter-spacing:.3px;text-shadow:0 1px 6px rgba(0,0,0,.5)}
.hero .controls{position:absolute;top:136px;left:0;right:0;font-size:7px;display:flex;justify-content:center;gap:22px}
.hero .tag{position:absolute;top:155px;left:0;right:0;font-family:'Tinos',serif;font-size:12px}
.arrow{position:absolute;top:128px;width:16px;height:16px;border:1px solid #cfd;border-radius:50%;opacity:.7}
.arrow.l{left:36px}.arrow.r{right:36px}
.dots{position:absolute;bottom:18px;left:0;right:0;display:flex;justify-content:center;gap:10px}
.dots span{width:16px;height:2px;background:#6d8c63}.dots span:first-child{background:#fff}

.heading{font-family:'Oswald',sans-serif;font-weight:600;color:var(--accent);text-align:center;text-transform:uppercase}
.copy{font-size:6.3px;line-height:12px;text-align:center;color:var(--soft)}
.serif-copy{font-family:'Tinos',serif;font-size:7.6px;line-height:12.5px;text-align:center;color:var(--soft)}

.intro{height:191px;background:var(--green-2);padding:33px 60px 0}
.intro .heading{font-size:17.5px;line-height:22px;margin-bottom:22px}
.intro .copy+.copy{margin-top:10px}

.strip{height:146px;display:flex}
.strip div{flex:1}

/* photo areas */
.ph-lab{background:radial-gradient(circle at 40% 35%,#e6ece4 0,transparent 35%),linear-gradient(135deg,#b9c8b4,#5f8a45 60%,#2f5a22)}
.ph-seedlings{background:radial-gradient(ellipse at 50% 10%,#c7e3a6 0,transparent 40%),linear-gradient(#6f8f52,#34422a 55%,#1d1d18)}
.ph-field{background:radial-gradient(circle at 60% 40%,#e9d6c6 0,transparent 22%),linear-gradient(135deg,#a6c27a,#5a8a35 60%,#3a6a24)}
.ph-oil{background:radial-gradient(circle at 35% 45%,#fff3a8 0,transparent 35%),linear-gradient(135deg,#f7d24a,#d79b12 60%,#a9740a)}
.ph-cream{background:radial-gradient(circle at 30% 40%,#f2f5e8 0,transparent 26%),linear-gradient(135deg,#c9e2ae,#7aa84e 60%,#4b7a2c)}
.ph-dropper{background:radial-gradient(circle at 55% 55%,#e8b92a 0,transparent 18%),linear-gradient(160deg,#f0ebd8,#c9c0a0 50%,#6f8a45)}
.ph-flower{background:radial-gradient(circle at 35% 40%,#8cc04c 0,transparent 35%),linear-gradient(135deg,#4f7f2c,#2f5a1c 60%,#c9c3b3)}
.ph-seed{background:radial-gradient(circle at 50% 55%,#6d5d47 0,transparent 30%),linear-gradient(160deg,#c8b89a,#8d765a 55%,#5c4a36)}
.ph-grower{background:radial-gradient(ellipse at 50% 0,#dfe7de 0,transparent 30%),linear-gradient(#8fb07a,#4f8a35 50%,#2a5220)}
.ph-farm{background:radial-gradient(ellipse at 70% 85%,#b52a25 0,transparent 18%),linear-gradient(#3f66a6 0%,#7f9cc8 40%,#b0a690 62%,#5f8a3a 78%,#3f6a28 100%)}
.ph-team1{background:radial-gradient(ellipse at 50% 0,#eef3f1 0,transparent 45%),linear-gradient(#c6d2cb,#6a8064 55%,#2a3a2a)}
.ph-team2{background:radial-gradient(circle at 50% 55%,#e8ecef 0,transparent 25%),linear-gradient(135deg,#6ea04c,#2f5e22 60%,#1a3515)}
.ph-market{background:radial-gradient(circle at 55% 50%,#2ecf4a 0,transparent 35%),linear-gradient(160deg,#0a1d0c,#0f6a22 60%,#071a09)}
.ph-community{background:radial-gradient(circle at 50% 45%,#eeeee8 0,transparent 28%),linear-gradient(135deg,#c6c8b6,#7e8a60 55%,#45592e)}
.ph-test{background:radial-gradient(circle at 70% 30%,#b7b3e6 0,transparent 22%),radial-gradient(circle at 65% 70%,#e8b828 0,transparent 14%),linear-gradient(160deg,#eef0f4,#b9c8b0 45%,#4f7a34)}
.ph-signup{background:radial-gradient(ellipse at 0 50%,#c5621c 0,transparent 38%),radial-gradient(ellipse at 80% 40%,#2f6a22 0,transparent 40%),linear-gradient(100deg,#5a3010 0%,#1c3a12 35%,#1b4a17 70%,#0e2a0c 100%)}

.offer{height:332px;padding:36px 50px 0}
.offer.tall{height:336px}
.offer .heading{font-size:17px;margin-bottom:10px}
.offer .serif-copy{margin-bottom:10px;padding:0 8px}
.cards{display:flex;gap:6px}
.card{width:143px;border:1px solid var(--line);height:193px;text-align:center}
.card .pic{height:104px}
.card h3{font-family:'Tinos',serif;font-weight:400;font-size:10px;margin:12px 0 6px}
.card p{font-size:5.4px;line-height:11.5px;color:var(--soft);padding:0 8px}
.card a{display:inline-block;margin-top:7px;font-size:6px;font-weight:700;color:var(--accent);text-decoration:none}

.badges{height:145px;background:var(--green-2);display:flex;justify-content:center;align-items:center;gap:26px}
.badges span{width:48px;height:48px;border-radius:50%;background:var(--badge);border:2px solid var(--badge-ring);box-shadow:inset 0 0 0 4px var(--badge),inset 0 0 0 5px var(--badge-ring)}
.badges span:nth-child(2),.badges span:nth-child(4){background:var(--badge-ring);box-shadow:inset 0 0 0 4px var(--badge)}

.farm{height:212px;display:flex;background:var(--green-2)}
.farm .text{width:270px;padding:38px 20px 0 50px}
.farm .heading{text-align:left;font-size:16px;margin-bottom:12px}
.farm .copy{text-align:left}
.outline{display:inline-block;margin-top:14px;border:1px solid var(--line);padding:4px 6px;font-size:6px;font-weight:700;color:var(--accent)}
.farm .pic{flex:1}

.team{height:345px;padding:38px 50px 0;text-align:center}
.team .heading{font-size:17px;margin-bottom:10px}
.team .serif-copy{margin-bottom:13px}
.team .row{display:flex;gap:8px}
.team .row div{flex:1;height:170px}
.team .outline{margin-top:18px}

.trust{height:333px;padding:36px 50px 0;background:var(--green)}
.trust .heading{font-size:17px;margin-bottom:10px}
.trust .serif-copy{margin-bottom:10px}

.signup{height:140px;text-align:center;padding-top:36px}
.signup h2{font-size:13.5px;font-weight:600;letter-spacing:.3px}
.signup p{font-size:6.2px;margin-top:5px}
.signup form{display:flex;justify-content:center;margin-top:12px}
.signup .field{width:185px;height:22px;background:#fff;color:#666;font-size:6px;text-align:left;padding:7px 8px}
.signup .send{width:60px;height:22px;background:var(--cta);font-size:6.5px;font-weight:700;padding-top:7px}

.footer{height:145px;background:var(--green);padding:28px 50px 0;position:relative}
.cols{display:flex}
.col h4{font-size:7px;font-weight:600;text-transform:uppercase;margin-bottom:9px}
.col p,.col li{font-size:5.4px;line-height:11px;color:var(--soft);list-style:none}
.col.about{width:146px;padding-right:12px}.col.links{width:100px}.col.contact{width:122px}
.icons{display:flex;gap:8px}
.icons span{width:12px;height:12px;border-radius:50%;border:1px solid var(--soft)}
.legal{position:absolute;left:50px;right:50px;bottom:10px;display:flex;justify-content:space-between;font-size:5.4px}
.legal nav{display:flex;gap:10px}

.gate-shade{position:absolute;inset:0;background:rgba(0,0,0,.62)}
.gate{position:absolute;top:48px;left:165px;width:204px;height:256px;border:2px solid #3fc23c;border-radius:10px;overflow:hidden;background:linear-gradient(#0d0d0d 0 52px,#1d2f18 52px);text-align:center}
.gate .brand{display:block;margin-top:19px;font-size:12px}
.gate h2{font-size:13px;font-weight:600;margin-top:16px}
.gate .select{margin:10px auto 0;width:146px;height:20px;background:#fff;color:#555;font-size:5.5px;text-align:left;padding:7px 6px;display:flex;justify-content:space-between}
.gate .dob{display:flex;align-items:center;justify-content:center;gap:4px;margin-top:9px}
.gate .dob b{font-size:6.5px;text-align:left;width:40px;line-height:8px}
.gate .dob span{border:1px solid #aaa;background:#fff;color:#555;font-size:6px;padding:6px 0;width:27px}
.gate .dob span:last-child{width:40px}
.gate .remember{display:flex;gap:6px;align-items:center;margin:8px 0 0 28px;text-align:left}
.gate .remember b{font-size:6px;display:block}
.gate .remember small{font-size:4.8px}
.gate .enter{margin:12px auto 0;width:146px;height:20px;background:var(--red);font-size:7px;font-weight:700;padding-top:6px}
.gate .fine{font-size:5px;line-height:8.5px;margin:10px 14px 0;font-weight:600}
</style>
</head>
<body>

<main class="page page--gated">
  <header class="topbar">
    <div class="social"><span></span><span></span><span></span></div>
    <span class="brand">kestrelbrookhollow.com</span>
    <div class="tools">
      <svg width="10" height="10" viewBox="0 0 10 10" fill="none" stroke="#ccc"><circle cx="4" cy="4" r="3"/><path d="M6.5 6.5 9 9"/></svg>
      <svg width="10" height="10" viewBox="0 0 10 10" fill="none" stroke="#ccc"><circle cx="5" cy="5" r="4.2"/><circle cx="5" cy="4" r="1.5"/></svg>
      <svg width="11" height="10" viewBox="0 0 11 10" fill="none" stroke="#ccc"><path d="M0 1h2l1.5 5h5.5l1.5-4H3"/><circle cx="4" cy="8.5" r=".8"/><circle cx="8" cy="8.5" r=".8"/></svg>
    </div>
  </header>
  <nav class="mainnav"><span class="on">Shop</span><span>For Producers</span><span>For Cultivators</span><span>Our Farm &amp; Facilities</span><span>Seed Genetics</span><span>Partner With Us</span></nav>
  <section class="hero" role="img" aria-label="Close-up of hemp leaves in a green field">
    <span class="arrow l"></span><span class="arrow r"></span>
  </section>
  <section class="intro">
    <h2 class="heading">Join us on a journey of growth as we pave the<br>way for Virginia hemp industry.</h2>
    <p class="copy">Lorem ipsum dolor sit amet, consectetur adipiscing elit, sed do eiusmod tempor int ut labore et dolore magna aliqua. Quis suspendisse ultrices gravida. Risus commodo viverra maecenas lacus vel facilisis.</p>
    <p class="copy">consectetur adipiscing elit, sed do eiusmod tempor incididunt ut labore et dolore magna aliqu ipsum suspendisse ultrices gravida. Risus commodo viverra maecenas accumsan lacus vel facilisis. Lorem ipsum dolor sit amet, consectetur adipiscing elit, sed do eiusmod tempor dolor sit amet, consectetur adipiscing elit, sed do eiusmod tempor</p>
  </section>
  <div class="strip">
    <div class="ph-lab" role="img" aria-label="Scientist inspecting hemp plants"></div>
    <div class="ph-seedlings" role="img" aria-label="Rows of potted hemp seedlings"></div>
    <div class="ph-field" role="img" aria-label="Farmer holding hemp in the field"></div>
  </div>
  <section class="offer">
    <h2 class="heading">For CBD Producers</h2>
    <p class="serif-copy">Lorem ipsum dolor sit amet, consectetur adipiscing elit, sed do eiusmod tempor int ut labore et dolore magna aliqua. Quis suspendisse ultrices gravida. Risus commodo viverra maecenas lacus vel facilisis.</p>
    <div class="cards">
      <article class="card"><div class="pic ph-oil" role="img" aria-label="Bottles of golden CBD oil"></div><h3>Wholesale CBD.</h3><p>Lorem ipsum doet, consectetur adipiscing elit, sed do eiusmod tempor innt ut labore et dolore magna aliqua. Quis ip se ultrices gravida.</p><a>More on Wholesale ›</a></article>
      <article class="card"><div class="pic ph-cream" role="img" aria-label="CBD cream with hemp leaf"></div><h3>White &amp; Private Label CBD.</h3><p>Lorem ipsum doet, consectetur adipiscing elit, sed do eiusmod tempor innt ut labore et dolore magna aliqua. Quis ip se ultrices gravida.</p><a>More on Wholesale ›</a></article>
      <article class="card"><div class="pic ph-dropper" role="img" aria-label="CBD dropper bottle beside hemp leaf"></div><h3>Highest Compliance</h3><p>Lorem ipsum doet, consectetur adipiscing elit, sed do eiusmod tempor innt ut labore et dolore magna aliqua. Quis ip se ultrices gravida.</p><a>More on Wholesale ›</a></article>
    </div>
  </section>
  <section class="badges" aria-label="Certifications"><span></span><span></span><span></span><span></span><span></span><span></span></section>
  <section class="offer tall">
    <h2 class="heading">For Hemp Cultivators.</h2>
    <p class="serif-copy">Lorem ipsum dolor sit amet, consectetur adipiscing elit, sed do eiusmod tempor int ut labore et dolore magna aliqua. Quis suspendisse ultrices gravida. Risus commodo viverra maecenas lacus vel facilisis.</p>
    <div class="cards">
      <article class="card"><div class="pic ph-flower" role="img" aria-label="Trimmed hemp flower being processed"></div><h3>Hemp Processing.</h3><p>Lorem ipsum doet, consectetur adipiscing elit, sed do eiusmod tempor innt ut labore et dolore magna aliqua. Quis ip se ultrices gravida.</p><a>More on Wholesale ›</a></article>
      <article class="card"><div class="pic ph-seed" role="img" aria-label="Gloved hand holding hemp seeds"></div><h3>Hemp Seed Genetics.</h3><p>Lorem ipsum doet, consectetur adipiscing elit, sed do eiusmod tempor innt ut labore et dolore magna aliqua. Quis ip se ultrices gravida.</p><a>More on Seed Genetics ›</a></article>
      <article class="card"><div class="pic ph-grower" role="img" aria-label="Grower standing among hemp in a greenhouse"></div><h3>Consultation</h3><p>Lorem ipsum doet, consectetur adipiscing elit, sed do eiusmod tempor innt ut labore et dolore magna aliqua. Quis ip se ultrices gravida.</p><a>Get In touch ›</a></article>
    </div>
  </section>
  <section class="farm">
    <div class="text">
      <h2 class="heading">Our Hemp Farm &amp; Facilities.</h2>
      <p class="copy">Lorem ipsum dolor sit amet, consectetur adiscing elit, sed do eiusmod tempor int ut labore et dolore magna aliqua. Quis suspendisse ultrices gravida. Risus commodo viverra maen lacus vel facilisis. Lorem ipsum dolor sit amet, consectetur adipiscing elit,ed do eiusmod tempor int ut labore et dolore magna aliqua. Quis susp disse ultrices gravida. Risus commodo viverra maecenan lacus vel facilisis.</p>
      <span class="outline">Our Facilities ›</span>
    </div>
    <div class="pic ph-farm" role="img" aria-label="Grain silos and red barn under blue sky"></div>
  </section>
  <section class="team">
    <h2 class="heading">Our Team.</h2>
    <p class="serif-copy">Lorem ipsum dolor sit amet, consectetur adipiscing elit, sed do eiusmod tempor int ut labore et dolore magna aliqua. Quis suspendisse ultrices gravida. Risus commodo viverra maecenas lacus vel facilisis.</p>
    <div class="row">
      <div class="ph-team1" role="img" aria-label="Two team members examining plants in a greenhouse"></div>
      <div class="ph-team2" role="img" aria-label="Team member in a lab coat among hemp plants"></div>
    </div>
    <span class="outline">Meet the Team ›</span>
  </section>
  <section class="trust">
    <h2 class="heading">The Source to Trust.</h2>
    <p class="serif-copy">Lorem ipsum dolor sit amet, consectetur adipiscing elit, sed do eiusmod tempor int ut labore et dolore magna aliqua. Quis suspendisse ultrices gravida. Risus commodo viverra maecenas lacus vel facilisis.</p>
    <div class="cards">
      <article class="card"><div class="pic ph-market" role="img" aria-label="Market ticker display"></div><h3>The CBD Market.</h3><p>Lorem ipsum doet, consectetur adipiscing elit, sed do eiusmod tempor innt ut labore et dolore magna aliqua. Quis ip se ultrices gravida.</p><a>Learn More ›</a></article>
      <article class="card"><div class="pic ph-community" role="img" aria-label="Researchers inspecting hemp together"></div><h3>Community</h3><p>Lorem ipsum doet, consectetur adipiscing elit, sed do eiusmod tempor innt ut labore et dolore magna aliqua. Quis ip se ultrices gravida.</p><a>Learn More ›</a></article>
      <article class="card"><div class="pic ph-test" role="img" aria-label="Gloved hands testing CBD oil"></div><h3>CBD Model Compliance.</h3><p>Lorem ipsum doet, consectetur adipiscing elit, sed do eiusmod tempor innt ut labore et dolore magna aliqua. Quis ip se ultrices gravida.</p><a>Learn More ›</a></article>
    </div>
  </section>
  <section class="signup ph-signup" role="img" aria-label="Hemp leaves at sunset behind the signup form">
    <h2>WE WANT TO STAY CONNECTED WITH YOU.</h2>
    <p>Join us as we pave the way for New York's hemp industry. Your privacy is important to us.</p>
    <form><span class="field">Enter Your Email</span><span class="send">SUBSCRIBE</span></form>
  </section>
  <footer class="footer">
    <div class="cols">
      <div class="col about"><h4>About Us</h4><p>Lorem ipsum dol et, consectetur adipiscing elit, sed do eiusmod or incididunt ut labore et dolore magna a. Quis ipsum suspendisse ultrices gravs commodo viverra maecenas accumsan lacus vel facilisis.</p></div>
      <div class="col links"><h4>Quick Links</h4><ul><li>Shop</li><li>For Producers</li><li>For Cultivators</li><li>Our Farm &amp; Facilities</li><li>Seed Genetics</li><li>Partner With Us</li></ul></div>
      <div class="col contact"><h4>Contacts Info</h4><p>⌖ 123 Avenue name, City name<br>&nbsp;&nbsp;&nbsp;10150, United States</p><p>☏ 888 888 8888</p><p>✉ info@kestrelbrookhollow.com</p></div>
      <div class="col"><h4>Stat Conected</h4><div class="icons"><span></span><span></span><span></span><span></span></div></div>
    </div>
    <div class="legal"><span>Copyright © 2020 KESTRELBROOKHOLLOW. All Rights Reserved.</span><nav><span>Terms &amp; Conditions</span><span>Privacy Policy</span><span>About Us</span><span>Support</span></nav></div>
  </footer>

  <div class="gate-shade"></div>
  <div class="gate" role="dialog" aria-label="Age verification">
    <span class="brand">kestrelbrookhollow.com</span>
    <h2>Age Verification</h2>
    <div class="select"><span>Where are you from</span><span>▾</span></div>
    <div class="dob"><b>Enter your birthday</b><span>DD</span><span>MM</span><span>YYYY</span></div>
    <div class="remember">
      <svg width="14" height="14" viewBox="0 0 14 14" fill="none" stroke="#fff"><circle cx="7" cy="7" r="6"/><path d="M4 7l2 2 4-5"/></svg>
      <div><b>Remember me for 30 days</b><small>I confirm that this is not a shared device</small></div>
    </div>
    <div class="enter">ENTER</div>
    <p class="fine">You must be legally old enough to purchase cannabis. Please note that we only deliver in Virginia. By entering this site, you agree to our Terms and Conditions &amp; Privacy Policy</p>
  </div>
</main>

<main class="page page--open">
  <header class="topbar">
    <div class="social"><span></span><span></span><span></span></div>
    <span class="brand">kestrelbrookhollow.com</span>
    <div class="tools">
      <svg width="10" height="10" viewBox="0 0 10 10" fill="none" stroke="#ccc"><circle cx="4" cy="4" r="3"/><path d="M6.5 6.5 9 9"/></svg>
      <svg width="10" height="10" viewBox="0 0 10 10" fill="none" stroke="#ccc"><circle cx="5" cy="5" r="4.2"/><circle cx="5" cy="4" r="1.5"/></svg>
      <svg width="11" height="10" viewBox="0 0 11 10" fill="none" stroke="#ccc"><path d="M0 1h2l1.5 5h5.5l1.5-4H3"/><circle cx="4" cy="8.5" r=".8"/><circle cx="8" cy="8.5" r=".8"/></svg>
    </div>
  </header>
  <nav class="mainnav"><span class="on">Shop</span><span>For Producers</span><span>For Cultivators</span><span>Our Farm &amp; Facilities</span><span>Seed Genetics</span><span>Partner With Us</span></nav>
  <section class="hero" role="img" aria-label="Close-up of hemp leaves in a green field">
    <span class="arrow l"></span><span class="arrow r"></span>
    <h1>KESTREL BROOK HOLLOW</h1>
    <div class="controls"><span>Pause</span><span>•</span><span>Play</span><span>•</span><span>Rewind</span></div>
    <p class="tag">Agriculture farming Hemp and CBD</p>
    <div class="dots"><span></span><span></span><span></span><span></span></div>
  </section>
  <section class="intro">
    <h2 class="heading">Join us on a journey of growth as we pave the<br>way for Virginia hemp industry.</h2>
    <p class="copy">Lorem ipsum dolor sit amet, consectetur adipiscing elit, sed do eiusmod tempor int ut labore et dolore magna aliqua. Quis suspendisse ultrices gravida. Risus commodo viverra maecenas lacus vel facilisis.</p>
    <p class="copy">consectetur adipiscing elit, sed do eiusmod tempor incididunt ut labore et dolore magna aliqu ipsum suspendisse ultrices gravida. Risus commodo viverra maecenas accumsan lacus vel facilisis. Lorem ipsum dolor sit amet, consectetur adipiscing elit, sed do eiusmod tempor dolor sit amet, consectetur adipiscing elit, sed do eiusmod tempor</p>
  </section>
  <div class="strip">
    <div class="ph-lab" role="img" aria-label="Scientist inspecting hemp plants"></div>
    <div class="ph-seedlings" role="img" aria-label="Rows of potted hemp seedlings"></div>
    <div class="ph-field" role="img" aria-label="Farmer holding hemp in the field"></div>
  </div>
  <section class="offer">
    <h2 class="heading">For CBD Producers</h2>
    <p class="serif-copy">Lorem ipsum dolor sit amet, consectetur adipiscing elit, sed do eiusmod tempor int ut labore et dolore magna aliqua. Quis suspendisse ultrices gravida. Risus commodo viverra maecenas lacus vel facilisis.</p>
    <div class="cards">
      <article class="card"><div class="pic ph-oil" role="img" aria-label="Bottles of golden CBD oil"></div><h3>Wholesale CBD.</h3><p>Lorem ipsum doet, consectetur adipiscing elit, sed do eiusmod tempor innt ut labore et dolore magna aliqua. Quis ip se ultrices gravida.</p><a>More on Wholesale ›</a></article>
      <article class="card"><div class="pic ph-cream" role="img" aria-label="CBD cream with hemp leaf"></div><h3>White &amp; Private Label CBD.</h3><p>Lorem ipsum doet, consectetur adipiscing elit, sed do eiusmod tempor innt ut labore et dolore magna aliqua. Quis ip se ultrices gravida.</p><a>More on Wholesale ›</a></article>
      <article class="card"><div class="pic ph-dropper" role="img" aria-label="CBD dropper bottle beside hemp leaf"></div><h3>Highest Compliance</h3><p>Lorem ipsum doet, consectetur adipiscing elit, sed do eiusmod tempor innt ut labore et dolore magna aliqua. Quis ip se ultrices gravida.</p><a>More on Wholesale ›</a></article>
    </div>
  </section>
  <section class="badges" aria-label="Certifications"><span></span><span></span><span></span><span></span><span></span><span></span></section>
  <section class="offer tall">
    <h2 class="heading">For Hemp Cultivators.</h2>
    <p class="serif-copy">Lorem ipsum dolor sit amet, consectetur adipiscing elit, sed do eiusmod tempor int ut labore et dolore magna aliqua. Quis suspendisse ultrices gravida. Risus commodo viverra maecenas lacus vel facilisis.</p>
    <div class="cards">
      <article class="card"><div class="pic ph-flower" role="img" aria-label="Trimmed hemp flower being processed"></div><h3>Hemp Processing.</h3><p>Lorem ipsum doet, consectetur adipiscing elit, sed do eiusmod tempor innt ut labore et dolore magna aliqua. Quis ip se ultrices gravida.</p><a>More on Wholesale ›</a></article>
      <article class="card"><div class="pic ph-seed" role="img" aria-label="Gloved hand holding hemp seeds"></div><h3>Hemp Seed Genetics.</h3><p>Lorem ipsum doet, consectetur adipiscing elit, sed do eiusmod tempor innt ut labore et dolore magna aliqua. Quis ip se ultrices gravida.</p><a>More on Seed Genetics ›</a></article>
      <article class="card"><div class="pic ph-grower" role="img" aria-label="Grower standing among hemp in a greenhouse"></div><h3>Consultation</h3><p>Lorem ipsum doet, consectetur adipiscing elit, sed do eiusmod tempor innt ut labore et dolore magna aliqua. Quis ip se ultrices gravida.</p><a>Get In touch ›</a></article>
    </div>
  </section>
  <section class="farm">
    <div class="text">
      <h2 class="heading">Our Hemp Farm &amp; Facilities.</h2>
      <p class="copy">Lorem ipsum dolor sit amet, consectetur adiscing elit, sed do eiusmod tempor int ut labore et dolore magna aliqua. Quis suspendisse ultrices gravida. Risus commodo viverra maen lacus vel facilisis. Lorem ipsum dolor sit amet, consectetur adipiscing elit,ed do eiusmod tempor int ut labore et dolore magna aliqua. Quis susp disse ultrices gravida. Risus commodo viverra maecenan lacus vel facilisis.</p>
      <span class="outline">Our Facilities ›</span>
    </div>
    <div class="pic ph-farm" role="img" aria-label="Grain silos and red barn under blue sky"></div>
  </section>
  <section class="team">
    <h2 class="heading">Our Team.</h2>
    <p class="serif-copy">Lorem ipsum dolor sit amet, consectetur adipiscing elit, sed do eiusmod tempor int ut labore et dolore magna aliqua. Quis suspendisse ultrices gravida. Risus commodo viverra maecenas lacus vel facilisis.</p>
    <div class="row">
      <div class="ph-team1" role="img" aria-label="Two team members examining plants in a greenhouse"></div>
      <div class="ph-team2" role="img" aria-label="Team member in a lab coat among hemp plants"></div>
    </div>
    <span class="outline">Meet the Team ›</span>
  </section>
  <section class="trust">
    <h2 class="heading">The Source to Trust.</h2>
    <p class="serif-copy">Lorem ipsum dolor sit amet, consectetur adipiscing elit, sed do eiusmod tempor int ut labore et dolore magna aliqua. Quis suspendisse ultrices gravida. Risus commodo viverra maecenas lacus vel facilisis.</p>
    <div class="cards">
      <article class="card"><div class="pic ph-market" role="img" aria-label="Market ticker display"></div><h3>The CBD Market.</h3><p>Lorem ipsum doet, consectetur adipiscing elit, sed do eiusmod tempor innt ut labore et dolore magna aliqua. Quis ip se ultrices gravida.</p><a>Learn More ›</a></article>
      <article class="card"><div class="pic ph-community" role="img" aria-label="Researchers inspecting hemp together"></div><h3>Community</h3><p>Lorem ipsum doet, consectetur adipiscing elit, sed do eiusmod tempor innt ut labore et dolore magna aliqua. Quis ip se ultrices gravida.</p><a>Learn More ›</a></article>
      <article class="card"><div class="pic ph-test" role="img" aria-label="Gloved hands testing CBD oil"></div><h3>CBD Model Compliance.</h3><p>Lorem ipsum doet, consectetur adipiscing elit, sed do eiusmod tempor innt ut labore et dolore magna aliqua. Quis ip se ultrices gravida.</p><a>Learn More ›</a></article>
    </div>
  </section>
  <section class="signup ph-signup" role="img" aria-label="Hemp leaves at sunset behind the signup form">
    <h2>WE WANT TO STAY CONNECTED WITH YOU.</h2>
    <p>Join us as we pave the way for New York's hemp industry. Your privacy is important to us.</p>
    <form><span class="field">Enter Your Email</span><span class="send">SUBSCRIBE</span></form>
  </section>
  <footer class="footer">
    <div class="cols">
      <div class="col about"><h4>About Us</h4><p>Lorem ipsum dol et, consectetur adipiscing elit, sed do eiusmod or incididunt ut labore et dolore magna a. Quis ipsum suspendisse ultrices gravs commodo viverra maecenas accumsan lacus vel facilisis.</p></div>
      <div class="col links"><h4>Quick Links</h4><ul><li>Shop</li><li>For Producers</li><li>For Cultivators</li><li>Our Farm &amp; Facilities</li><li>Seed Genetics</li><li>Partner With Us</li></ul></div>
      <div class="col contact"><h4>Contacts Info</h4><p>⌖ 123 Avenue name, City name<br>&nbsp;&nbsp;&nbsp;10150, United States</p><p>☏ 888 888 8888</p><p>✉ info@kestrelbrookhollow.com</p></div>
      <div class="col"><h4>Stat Conected</h4><div class="icons"><span></span><span></span><span></span><span></span></div></div>
    </div>
    <div class="legal"><span>Copyright © 2020 KESTRELBROOKHOLLOW. All Rights Reserved.</span><nav><span>Terms &amp; Conditions</span><span>Privacy Policy</span><span>About Us</span><span>Support</span></nav></div>
  </footer>
</main>

</body>
</html>
```